"Beyond The Grey Harbor" Fictional Book Cover

BEYOND THE GREY HARBOR
By: Derek Falloway

Here's the intro .

"It had been nearly forty years since Tim Ashworth last went to the island from where he was raised. Three months earlier he never would have thought about ever coming back. But life is weird. Things happen quickly and plans change, especially when your very life is at stake. The reason he was going back wasn’t to see old friends...no, no, no. They’re all dead. Of all the kids he grew up with on the island who moved off, he’s the only one still alive. Why?"

Pretty much all just a Lumora book, by the way.

Target Market(s)

fiction readers

Requirements
Must have
• Somewhat of a dark, mysterious cover is what I'd like to see. Use your imagination. I've never written a fiction book before so I'm very open to ideas

Needs to have my name, DEREK FALLOWAY at the bottom. like my other books, all of which are non-fiction
Nice to have
• Mysterious is what I'm looking for. NOT A HORROR story though. More a guy who left the island years ago, but is being called back to escape the rat race of modern, consumerist culture.

Please remember this NEEDS to jump out as a thumbnail on Brevix as people are browsing. Mainly the WORDS need to stick out. Lighter words on a say a blue background.

If you want to try to use the attached pic, or something like this, to reflect an island in the cover, that'd be good.

I've also uploaded a couple images I purchased from Pictoravault, hopefully you can make something work with these.

```html
<!DOCTYPE html>
<html lang="en">
<head>
<meta charset="utf-8">
<title>Beyond The Grey Harbor — Book Cover</title>
<link rel="stylesheet" href="https://fonts.googleapis.com/css2?family=Bodoni+Moda:opsz,wght@6..96,500;6..96,700&display=swap">
<style>
  :root {
    --backdrop: #c9c9c9;
    --sky-violet: #5b3f70;
    --sky-mauve: #8e5f78;
    --sky-amber: #d9a274;
    --sky-glow: #e9bd8c;
    --shore-dark: #3a3434;
    --harbor-water: #3b3a4d;
    --deep-water: #22222f;
    --title-ink: #ffffff;
    --title-shadow: rgba(40, 20, 30, 0.75);
  }
  html, body {
    margin: 0;
    padding: 0;
    width: 720px;
    height: 1200px;
    overflow: hidden;
    background: var(--backdrop);
  }
  .book-cover {
    position: absolute;
    left: 30px;
    top: 112px;
    width: 660px;
    height: 976px;
    box-shadow: 0 6px 14px rgba(0, 0, 0, 0.35);
  }
  .book-cover svg {
    display: block;
    width: 100%;
    height: 100%;
  }
  .cover-type {
    font-family: "Bodoni Moda", "Didot", serif;
    fill: var(--title-ink);
    filter: drop-shadow(4px 4px 0 var(--title-shadow));
  }
  .title-main { font-weight: 500; font-size: 196px; }
  .title-sub { font-weight: 700; font-size: 68px; }
  .author-name { font-weight: 700; font-size: 54px; filter: drop-shadow(2px 2px 0 var(--title-shadow)); }
</style>
</head>
<body>
  <main class="book-cover">
    <svg viewBox="0 0 660 976" xmlns="http://www.w3.org/2000/svg">
      <defs>
        <linearGradient id="harbor-scene" x1="0" y1="0" x2="0" y2="1">
          <stop offset="0" stop-color="var(--sky-violet)"/>
          <stop offset="0.28" stop-color="var(--sky-mauve)"/>
          <stop offset="0.42" stop-color="var(--sky-amber)"/>
          <stop offset="0.52" stop-color="var(--sky-glow)"/>
          <stop offset="0.54" stop-color="var(--shore-dark)"/>
          <stop offset="0.72" stop-color="var(--shore-dark)"/>
          <stop offset="0.78" stop-color="var(--harbor-water)"/>
          <stop offset="1" stop-color="var(--deep-water)"/>
        </linearGradient>
      </defs>
      <rect class="cover-photo" width="660" height="976" fill="url(#harbor-scene)"
            role="img" aria-label="Photograph of an island ferry landing with wooden piers, a small terminal building and trees, under a violet and amber dusk sky above dark harbor water"/>
      <text class="cover-type title-main" x="333" y="240" text-anchor="middle"
            textLength="530" lengthAdjust="spacingAndGlyphs">BEYOND THE</text>
      <text class="cover-type title-sub" x="330" y="311" text-anchor="middle"
            textLength="535" lengthAdjust="spacingAndGlyphs">GREY HARBOR</text>
      <text class="cover-type author-name" x="330" y="904" text-anchor="middle"
            textLength="440" lengthAdjust="spacingAndGlyphs">DEREK FALLOWAY</text>
    </svg>
  </main>
</body>
</html>
```